Brand Identity Stationary Package

Hello I'm looking for a full branding package for my Property Management Company. I have a logo but looking to have the following
Business Card
Email signature
Facebook cover photo
Letterhead (word.doc)
#10 Envelope
Pocket Folder - link to 9x12 pocket folder design specs https://www.printorbit-example.ca/marketing-materials/presentation-folders
would like everything to match and be brand identifiable. The company looks after residential properties/apartments and some commercial properties. Attached is a zip of the files.
For Business Card
Name: Gareth Lindqvist
Position: Operations Manager
Number: 1 (555) 384-2917
Email: Gareth@harborkey-example.ca
Website: Harborkey-example.ca
Property Management

```html
<!DOCTYPE html>
<html lang="en">
<head>
<meta charset="utf-8">
<title>Harborkey Property Management – #10 Envelope</title>
<link rel="stylesheet" href="https://fonts.googleapis.com/css2?family=Montserrat:wght@500;600&family=Source+Sans+3:wght@400&display=swap">
<style>
  :root {
    --brand-green: #7fa642;
    --ink: #0b0b0b;
    --paper: #f3f2f2;
    --backdrop: #d0cfcf;
    --on-green: #f4f4f2;
  }
  html, body {
    margin: 0;
    padding: 0;
    overflow: hidden;
  }
  body {
    width: 1200px;
    height: 1050px;
    background: var(--backdrop);
    position: relative;
    font-family: "Source Sans 3", "Segoe UI", sans-serif;
  }
  .envelope {
    position: absolute;
    left: 145px;
    width: 910px;
    height: 390px;
    background: var(--paper);
    overflow: hidden;
  }
  .envelope--back { top: 105px; }
  .envelope--front { top: 556px; }
  .envelope svg.artwork {
    position: absolute;
    inset: 0;
    width: 100%;
    height: 100%;
  }
  .wordmark {
    position: absolute;
    font-family: "Montserrat", sans-serif;
    font-weight: 600;
    line-height: 1;
    margin: 0;
  }
  .wordmark__name {
    display: block;
    letter-spacing: 0.06em;
  }
  .wordmark__tagline {
    display: block;
    font-weight: 500;
    letter-spacing: 0.62em;
  }
  .envelope--back .wordmark {
    left: 0;
    right: 0;
    top: 34px;
    text-align: center;
    color: var(--on-green);
  }
  .envelope--back .wordmark__name { font-size: 46px; }
  .envelope--back .wordmark__tagline {
    font-size: 11px;
    margin-top: 9px;
    padding-left: 0.62em;
  }
  .envelope--front .wordmark {
    left: 52px;
    top: 62px;
    color: var(--ink);
  }
  .envelope--front .wordmark__name { font-size: 40px; }
  .envelope--front .wordmark__tagline {
    font-size: 10px;
    margin-top: 8px;
  }
  .contact-list {
    position: absolute;
    left: 52px;
    top: 145px;
    margin: 0;
    padding: 0;
    list-style: none;
    color: var(--ink);
    font-size: 20px;
  }
  .contact-list li {
    display: flex;
    align-items: center;
    height: 26px;
  }
  .contact-list svg {
    width: 16px;
    height: 16px;
    margin-right: 13px;
    fill: var(--brand-green);
  }
</style>
</head>
<body>

  <section class="envelope envelope--back" aria-label="Envelope back with flap">
    <svg class="artwork" viewBox="0 0 1552 665" preserveAspectRatio="none" aria-hidden="true">
      <path d="M0,0 L1552,0 L1508,150 C1490,200 1452,223 1420,223 L132,223 C100,223 62,200 44,150 Z" fill="var(--brand-green)"/>
    </svg>
    <h1 class="wordmark">
      <span class="wordmark__name">HARBORKEY</span>
      <span class="wordmark__tagline">PROPERTY MANAGEMENT</span>
    </h1>
  </section>

  <section class="envelope envelope--front" aria-label="Envelope front">
    <svg class="artwork" viewBox="0 0 1552 665" preserveAspectRatio="none" aria-hidden="true">
      <path class="swoosh" d="M0,497 C120,560 300,575 520,555 C800,530 1050,430 1250,412 C1350,405 1420,425 1462,440 C1400,428 1330,424 1250,430 C1000,450 700,560 420,605 C250,625 100,600 0,552 Z" fill="var(--ink)"/>
      <path class="wave" d="M0,565 C120,625 300,640 500,615 C800,575 1050,440 1280,432 C1400,428 1480,455 1552,482 L1552,665 L0,665 Z" fill="var(--brand-green)"/>
    </svg>
    <div class="wordmark">
      <span class="wordmark__name">HARBORKEY</span>
      <span class="wordmark__tagline">PROPERTY MANAGEMENT</span>
    </div>
    <ul class="contact-list">
      <li>
        <svg viewBox="0 0 16 16" aria-hidden="true"><path d="M1,6 C1,3 4,2 8,2 C12,2 15,3 15,6 L12,6.5 L11,4.5 L5,4.5 L4,6.5 Z M4,8 L12,8 L14,14 L2,14 Z"/></svg>
        1 (555) 384-2917
      </li>
      <li>
        <svg viewBox="0 0 16 16" aria-hidden="true"><path d="M1,3 L15,3 L8,9 Z M1,4.5 L8,10.5 L15,4.5 L15,13 L1,13 Z"/></svg>
        Gareth@harborkey-example.ca
      </li>
      <li>
        <svg viewBox="0 0 16 16" aria-hidden="true"><circle cx="8" cy="8" r="7"/><path d="M5,3 C7,4 6,6 4,7 C3,8 4,10 6,10 C7,11 6,13 7,14" fill="none" stroke="var(--paper)" stroke-width="1.4"/><path d="M10,2.5 C9.5,4 11,5 12.5,5.5" fill="none" stroke="var(--paper)" stroke-width="1.2"/></svg>
        www.Harborkey-example.ca
      </li>
    </ul>
  </section>

</body>
</html>
```